Business Card Design

WE are looking for a premium quality Business Cards for a Law Firm . Copies of our current business card is attached.

Contact Information for Business Card

xyz

```html
<!DOCTYPE html>
<html lang="en">
<head>
<meta charset="utf-8">
<title>Thornbury Lawyers – Business Card</title>
<link rel="stylesheet" href="https://fonts.googleapis.com/css2?family=Open+Sans:wght@400;600;700&display=swap">
<style>
  :root {
    --bg: #e4e3e0;
    --paper: #ffffff;
    --gold: #d4ac62;
    --green: #0f2a1e;
    --white: #ffffff;
  }
  * { box-sizing: border-box; margin: 0; padding: 0; }
  html, body { width: 1200px; height: 801px; overflow: hidden; }
  body {
    background: var(--bg);
    font-family: "Open Sans", Arial, sans-serif;
    color: var(--green);
    position: relative;
  }
  .card {
    position: absolute;
    top: 246px;
    width: 540px;
    height: 309px;
    border-radius: 18px;
    box-shadow: 0 6px 18px rgba(0,0,0,0.12);
    overflow: hidden;
  }
  .card-front { left: 40px; background: var(--paper); border: 3px solid var(--gold); }
  .card-back { left: 620px; background: var(--gold); }

  /* front: brand block */
  .brand {
    position: absolute;
    left: 0; top: 0;
    width: 262px; height: 100%;
    display: flex; flex-direction: column;
    align-items: center; justify-content: center;
    gap: 16px;
  }
  .brand-mark {
    width: 76px; height: 76px;
    border: 4px solid var(--gold);
    border-radius: 50%;
  }
  .brand-name {
    font-weight: 700;
    font-size: 18px;
    letter-spacing: 1.5px;
    text-transform: uppercase;
    color: var(--green);
  }
  .divider {
    position: absolute;
    left: 262px; top: 38px;
    width: 1.5px; height: 230px;
    background: var(--green);
  }

  /* front: contact block */
  .contact {
    position: absolute;
    left: 284px; top: 36px;
    width: 240px;
    font-size: 11.5px;
    line-height: 1.45;
  }
  .person-name { font-size: 21px; font-weight: 700; line-height: 1.1; letter-spacing: 0.3px; }
  .person-role { font-size: 10.5px; text-transform: uppercase; }
  .person-quals { font-size: 11px; margin-bottom: 12px; }
  .contact-list { list-style: none; margin-bottom: 12px; }
  .contact-list li { display: flex; align-items: center; gap: 7px; }
  .contact-list svg { width: 11px; height: 11px; fill: var(--green); flex: none; }
  .address { font-style: normal; font-size: 11.5px; }

  /* back */
  .back-inner {
    position: absolute; inset: 0;
    display: flex; flex-direction: column;
    align-items: center; justify-content: center;
    gap: 22px;
  }
  .back-mark {
    width: 118px; height: 118px;
    border: 6px solid var(--white);
    border-radius: 50%;
  }
  .back-name {
    font-weight: 700;
    font-size: 32px;
    letter-spacing: 2px;
    text-transform: uppercase;
    color: var(--green);
  }
</style>
</head>
<body>

<section class="card card-front" aria-label="Business card front">
  <div class="brand">
    <div class="brand-mark"></div>
    <div class="brand-name">Thornbury Lawyers</div>
  </div>
  <div class="divider"></div>
  <div class="contact">
    <div class="person-name">DANIEL REEVE</div>
    <div class="person-role">Director &amp; Principal Solicitor</div>
    <div class="person-quals">MBA, Juris Doctor</div>
    <ul class="contact-list">
      <li><svg viewBox="0 0 12 12"><path d="M2.5 1 4.5 3 3.6 4.6a6 6 0 0 0 3.8 3.8L9 7.5l2 2-1.3 1.6C5.5 11 1 6.5 0.9 2.3Z"/></svg>+61 7 3000 4812</li>
      <li><svg viewBox="0 0 12 12"><path d="M3 0.5h6v11H3Zm1 1.3v7.6h4V1.8Z"/></svg>+61 0400 000 217</li>
      <li><svg viewBox="0 0 12 12"><path d="M0.5 2.5h11v7h-11Zm1 1 4.5 3 4.5-3v-0.2h-9Z"/></svg>daniel@thornburylawyers.com.au</li>
      <li><svg viewBox="0 0 12 12"><circle cx="6" cy="6" r="5.5"/></svg>www.thornburylawyers.com.au</li>
    </ul>
    <address class="address">
      Level 3, Thornbury House,<br>
      48 Harbour Street,<br>
      Milton, QLD 4064
    </address>
  </div>
</section>

<section class="card card-back" aria-label="Business card back">
  <div class="back-inner">
    <div class="back-mark"></div>
    <div class="back-name">Thornbury Lawyers</div>
  </div>
</section>

</body>
</html>
```